Business Card Design for Varomir Facility Services

We are looking for a Business Card Design for the Company "Varomir Facility Services."
Front side:
- Company Logo (small)
- Company Name, address, pohone, website and personal data.
- white background, for text e.g. company colors (blue or green like in the logo)
Please use following data:
Company data:
Varomir Facility Services Kostelac
Birkenhaldweg 14
6330 Cham
www.varomir-fs.ch
Person data:
Tarik Kostelac
Geschäftsführer
+41 76 519 47 83
info@varomir-fs.ch
Back side:
could be colored in blue or green
please use a big logo sing and some smaller icons to say what is all beeing offered in facility services, like cleaning, maintenance cleaning
industrial cleaning, caretaking, gardening, disposal. There is no need for everyone of the icons if there are similar or an icon is standing for more of them.
colors to use:
blue: HEX 246BB0
green: HEX 52B33E

```html
<!DOCTYPE html>
<html lang="de">
<head>
<meta charset="utf-8">
<title>Varomir Facility Services – Visitenkarte</title>
<link rel="stylesheet" href="https://fonts.googleapis.com/css2?family=Arimo:wght@400;700&display=swap">
<style>
  :root {
    --brand-blue: #246BB0;
    --brand-blue-dark: #1D55A6;
    --brand-green: #52B33E;
    --ink-grey: #5A5F66;
    --paper: #FFFFFF;
    --backdrop: #E9ECEF;
  }
  * { box-sizing: border-box; margin: 0; padding: 0; }
  html, body { width: 1200px; height: 800px; overflow: hidden; }
  body {
    background: var(--backdrop);
    font-family: "Arimo", Arial, sans-serif;
    position: relative;
  }
  .card {
    position: absolute;
    top: 225px;
    width: 540px;
    height: 350px;
    overflow: hidden;
    box-shadow: 0 6px 18px rgba(0,0,0,0.15);
  }

  /* Back side */
  .card--back {
    left: 40px;
    background: linear-gradient(135deg, var(--brand-green) 0%, #3FA06A 45%, var(--brand-blue) 100%);
    color: var(--paper);
    text-align: center;
  }
  .back-logo {
    position: absolute;
    top: 105px;
    left: 0; right: 0;
    display: flex;
    justify-content: center;
    align-items: center;
    gap: 14px;
  }
  .back-logo .logo-dot {
    width: 22px; height: 22px; border-radius: 50%;
    background: var(--paper);
  }
  .back-logo .logo-name {
    font-weight: 700;
    font-size: 34px;
    letter-spacing: 1px;
    color: var(--paper);
  }
  .service-list {
    position: absolute;
    top: 228px;
    left: 0; right: 0;
    font-size: 13px;
    line-height: 1.6;
  }

  /* Front side */
  .card--front {
    left: 620px;
    background: var(--paper);
  }
  .front-logo {
    position: absolute;
    top: 78px;
    left: 60px;
    display: flex;
    align-items: center;
    gap: 12px;
  }
  .front-logo .logo-dot {
    width: 20px; height: 20px; border-radius: 50%;
    background: var(--brand-green);
  }
  .front-logo .logo-name {
    font-weight: 700;
    font-size: 30px;
    letter-spacing: 1px;
    color: var(--brand-blue-dark);
  }
  .divider {
    position: absolute;
    top: 196px;
    left: 200px;
    right: 28px;
    height: 1px;
    background: var(--brand-blue-dark);
  }
  .person {
    position: absolute;
    left: 36px;
    top: 184px;
  }
  .person-name {
    font-weight: 700;
    font-size: 19px;
    color: var(--brand-blue-dark);
  }
  .person-role {
    font-size: 15px;
    color: var(--brand-green);
    margin-top: 3px;
  }
  .company {
    position: absolute;
    left: 300px;
    top: 212px;
  }
  .company-name {
    font-weight: 700;
    font-size: 13px;
    color: var(--ink-grey);
    margin-bottom: 8px;
  }
  .contact-list { list-style: none; margin-top: 14px; }
  .company .contact-list { margin-top: 0; }
  .contact-item {
    display: flex;
    align-items: center;
    gap: 8px;
    font-size: 13px;
    color: var(--ink-grey);
    margin-bottom: 8px;
  }
  .contact-item svg { width: 16px; height: 16px; flex: none; }
  .bottom-band {
    position: absolute;
    left: 0; right: 0; bottom: 0;
    height: 12px;
    display: flex;
  }
  .bottom-band .band-blue { flex: 0 0 58%; background: var(--brand-blue-dark); }
  .bottom-band .band-green { flex: 1; background: var(--brand-green); }
</style>
</head>
<body>

<section class="card card--back" aria-label="Rückseite">
  <div class="back-logo">
    <span class="logo-dot"></span>
    <span class="logo-name">Varomir Facility Services</span>
  </div>
  <p class="service-list">
    facility services | like cleaning | maintenance cleaning | industrial cleaning<br>
    caretaking | gardening | disposal
  </p>
</section>

<section class="card card--front" aria-label="Vorderseite">
  <div class="front-logo">
    <span class="logo-dot"></span>
    <span class="logo-name">Varomir Facility Services</span>
  </div>

  <div class="divider"></div>

  <div class="person">
    <p class="person-name">Tarik Kostelac</p>
    <p class="person-role">Geschäftsführer</p>
    <ul class="contact-list">
      <li class="contact-item">
        <svg viewBox="0 0 16 16" aria-hidden="true"><circle cx="8" cy="8" r="8" fill="var(--brand-blue-dark)"/><rect x="5.5" y="3.5" width="5" height="9" rx="1" fill="none" stroke="#fff" stroke-width="1.2"/></svg>
        +41 76 519 47 83
      </li>
      <li class="contact-item">
        <svg viewBox="0 0 16 16" aria-hidden="true"><circle cx="8" cy="8" r="8" fill="var(--brand-blue-dark)"/><rect x="4" y="5" width="8" height="6" fill="none" stroke="#fff" stroke-width="1.1"/><path d="M4 5 L8 8.5 L12 5" fill="none" stroke="#fff" stroke-width="1.1"/></svg>
        info@varomir-fs.ch
      </li>
    </ul>
  </div>

  <div class="company">
    <p class="company-name">Varomir Facility Services Kostelac</p>
    <ul class="contact-list">
      <li class="contact-item">
        <svg viewBox="0 0 16 16" aria-hidden="true"><circle cx="8" cy="8" r="8" fill="var(--brand-blue-dark)"/><path d="M8 12.5 C6 10 5 8.6 5 7 A3 3 0 0 1 11 7 C11 8.6 10 10 8 12.5Z" fill="#fff"/><circle cx="8" cy="7" r="1.1" fill="var(--brand-blue-dark)"/></svg>
        Birkenhaldweg 14, 6330 Cham
      </li>
      <li class="contact-item">
        <svg viewBox="0 0 16 16" aria-hidden="true"><circle cx="8" cy="8" r="8" fill="var(--brand-blue-dark)"/><circle cx="8" cy="8" r="4" fill="none" stroke="#fff" stroke-width="1.1"/><ellipse cx="8" cy="8" rx="1.8" ry="4" fill="none" stroke="#fff" stroke-width="1"/><line x1="4" y1="8" x2="12" y2="8" stroke="#fff" stroke-width="1"/></svg>
        www.varomir-fs.ch
      </li>
    </ul>
  </div>

  <div class="bottom-band">
    <span class="band-blue"></span>
    <span class="band-green"></span>
  </div>
</section>

</body>
</html>
```